Design a logo and an adult website to upload our amateur mature milf videos filmed on Maui*

Aloha,

We need a website and a logo design for my adult website, we have a domain already. Sirenablush.com via Netkite, We are based on the island of Maui, Hawaii. We'd like to feature the word "Filmed in Tropical Locations" instead of Maui though. We want to upload amateur solo girl videos and would like to have customers be able to be driven to our site to view short clips and then become members via a monthly membership. We'd also like to be able to have an area where we can post links to items that the customer can purchase that I can wear, use, etc. I'm new to all of this, so you'll have your work cut out for you. I'm open to more suggestions. The genre for my videos is amateur mature milf.

Thank you so much!
Updates

Target Market(s)

anyone interested in mature amateur milf videos

Industry/Entity Type

Adult

Coding

Coded - Design and coding required

Number of Pages Required

1 page

Font styles to use
Script

Requirements
Must have
• able to upload many videos; membership area; store area for customers to buy me toys, costumes and outfits to wear on camera; sneak peak area to view short clips for free. Area for still photos. Categories for videos: Outdoor videos; Naughty Costumes; Slutty Whore-Shoes;
Nice to have
• I like black and hot pink as colors, but I am very open to your ideas and designs. I'm a flashy, rhinestone and hot pink kinda girl, fyi. Let's keep it fun and sexy! :)

For the logo I would like pink kiss lips next to the lettering Sirena Blush. I have uploaded a sample of what I designed. It says .com in it, but please remove that part. Thanks!
Should not have
• Please do not use Maui or Hawaii. I don't want people to know where I reside. Please use the words Exotic tropical locations, instead.

```html
<!DOCTYPE html>
<html lang="en">
<head>
<meta charset="utf-8">
<title>Sirena Blush</title>
<link rel="stylesheet" href="https://fonts.googleapis.com/css2?family=Dancing+Script:wght@400;600;700&family=Tinos:wght@400;700&display=swap">
<style>
:root{
  --pink:#ff0a78;
  --pink-deep:#e0005f;
  --black:#000;
  --ink:#fff;
  --panel:#0b0b0b;
  --footer:#131313;
  --line:#2a2a2a;
}
*{margin:0;padding:0;box-sizing:border-box}
html,body{width:1200px;height:4101px;overflow:hidden;background:var(--black);color:var(--ink)}
body{position:relative;font-family:"Tinos",serif}
.script{font-family:"Dancing Script",cursive}
.abs{position:absolute}
.pink{color:var(--pink)}

/* header + hero */
.hero{position:absolute;left:0;top:0;width:1200px;height:557px;background:radial-gradient(ellipse at 70% 40%,#2a2a2a 0%,#0c0c0c 60%,#000 100%)}
.brand{position:absolute;display:flex;align-items:center;gap:12px;font-family:"Dancing Script",cursive;font-weight:600;color:var(--pink)}
.brand-dot{border-radius:50%;background:var(--pink)}
.nav{position:absolute;top:28px;left:492px;display:flex;gap:42px;font-family:"Dancing Script",cursive;font-size:20px;color:var(--pink)}
.nav a{color:inherit;text-decoration:none}
.nav a.active{color:var(--ink)}
.welcome{left:280px;top:195px;font-size:44px;font-family:"Dancing Script",cursive}
.hero-title{left:168px;top:205px;font-size:112px;line-height:1.1;font-family:"Dancing Script",cursive;font-weight:600;color:var(--pink);white-space:nowrap}
.btn{position:absolute;display:flex;align-items:center;justify-content:center;border-radius:30px;font-family:"Dancing Script",cursive;font-size:25px}
.btn-fill{background:var(--pink);color:var(--ink)}
.btn-line{border:2px solid var(--ink);color:var(--ink)}
.btn-pink-line{border:2px solid var(--pink);color:var(--pink)}
.band{position:absolute;left:0;top:557px;width:1200px;height:263px;background:linear-gradient(90deg,#ff0a78 0%,#ff1c80 55%,#d3005a 100%)}
.band-title{left:172px;top:570px;font-size:70px;line-height:82px;font-family:"Dancing Script",cursive}
.hero-photo{left:684px;top:64px;width:516px;height:756px;background:linear-gradient(180deg,#3a1a22 0%,#8a1040 55%,#d0125f 100%);border-radius:40% 40% 0 0 / 12% 12% 0 0}

/* section titles */
.section-title{position:absolute;left:0;width:1200px;text-align:center;font-family:"Dancing Script",cursive;font-size:64px}

/* categories */
.cat-img{position:absolute;top:977px;width:274px;height:258px}
.cat-label{position:absolute;width:274px;text-align:center;font-family:"Dancing Script",cursive;font-size:34px;line-height:36px}

/* video cards */
.card{position:absolute;width:198px;height:233px;border:1px solid var(--line);background:var(--panel)}
.card.featured{border-color:var(--pink)}
.thumb{height:175px;position:relative}
.tag{position:absolute;left:0;top:0;background:var(--pink);font-size:11px;font-weight:700;padding:3px 7px}
.play{position:absolute;left:79px;top:68px;width:40px;height:40px}
.card-foot{display:flex;align-items:center;height:56px;padding:0 10px;gap:9px}
.avatar{width:28px;height:28px;border-radius:50%;background:linear-gradient(135deg,#e9a3b8,#8a4a5a)}
.caption{font-size:11px;font-weight:700;line-height:12px;flex:1}
.share{width:18px;height:18px}

/* membership */
.member{position:absolute;left:0;top:2204px;width:1200px;height:502px;background:linear-gradient(135deg,#ff1a82 0%,#ff0a78 50%,#e6006a 100%)}
.member-title{left:172px;top:2290px;font-size:72px;line-height:82px;font-family:"Dancing Script",cursive;font-weight:600}
.member-text{left:172px;top:2468px;width:390px;font-size:16.5px;line-height:22.5px}
.price-line{position:absolute;left:574px;top:2204px;width:3px;height:102px;background:var(--ink)}
.price{position:absolute;left:521px;top:2306px;width:108px;height:108px;border:3px solid var(--ink);border-radius:50%;display:flex;align-items:center;justify-content:center;font-family:"Dancing Script",cursive;font-size:40px}
.member-photo{left:748px;top:2222px;width:287px;height:484px;background:linear-gradient(180deg,#f3c9a0 0%,#f07ab0 60%,#ff3d95 100%);border-radius:45% 45% 0 0 / 20% 20% 0 0}

/* store */
.product{position:absolute;top:2900px;width:254px;height:366px;border:2px solid var(--pink-deep)}
.product-img{position:absolute;left:50%;transform:translateX(-50%)}
.product-name{position:absolute;top:190px;width:100%;text-align:center;font-family:"Dancing Script",cursive;font-size:26px;line-height:24px;color:var(--pink)}
.product-text{position:absolute;width:100%;text-align:center;font-size:14.5px;line-height:23px}
.product .btn{left:55px;top:285px;width:142px;height:38px;font-size:22px}

/* stills */
.stills{position:absolute;left:0;top:3326px;width:1200px;height:534px;background:linear-gradient(90deg,#050505,#111 50%,#050505)}
.stills-photo{left:159px;top:3326px;width:430px;height:534px;background:linear-gradient(90deg,#2a1a18 0%,#8a2030 50%,#c41e3a 100%)}
.stills-title{left:624px;top:3505px;font-size:64px;font-family:"Dancing Script",cursive}
.stills-text{left:624px;top:3598px;width:410px;font-size:16.5px;line-height:22.5px}
.arrow{position:absolute;top:3604px;width:36px;height:68px}

/* footer */
.footer{position:absolute;left:0;top:3860px;width:1200px;height:241px;background:var(--footer)}
.social{position:absolute;top:3922px;left:460px;display:flex;gap:34px}
.social span{width:32px;height:32px;border-radius:50%;background:var(--pink)}
.copy{position:absolute;left:0;top:3978px;width:1200px;text-align:center;font-size:15px}
</style>
</head>
<body>

<!-- Hero -->
<header class="hero"></header>
<div class="band"></div>
<div class="abs hero-photo" role="img" aria-label="Model in pink lingerie posing against a dark wall"></div>

<div class="brand" style="left:172px;top:20px;font-size:32px"><span class="brand-dot" style="width:30px;height:30px"></span>Sirena Blush</div>
<nav class="nav">
  <a class="active" href="#">Home</a><a href="#">About</a><a href="#">Videos</a><a href="#">Products</a><a href="#">Memberships</a><a href="#">Contact</a>
</nav>

<div class="abs welcome">Welcome to</div>
<h1 class="abs hero-title" style="top:215px">Sirena Blush</h1>
<a class="btn btn-fill" style="left:248px;top:349px;width:174px;height:50px">Upload Videos</a>
<a class="btn btn-fill" style="left:436px;top:349px;width:174px;height:50px">Share Videos</a>

<h2 class="abs band-title">Filmed in<br>Tropical Locations</h2>
<a class="btn btn-line" style="left:170px;top:752px;width:170px;height:40px;font-size:22px">View Locations</a>

<!-- Categories -->
<h2 class="section-title" style="top:868px">Video <span class="pink">Categories</span></h2>
<div class="cat-img" style="left:172px;background:linear-gradient(180deg,#7fa8c9 0%,#2f5a2a 45%,#1fc2a4 100%)" role="img" aria-label="Tropical resort over turquoise water"></div>
<div class="cat-img" style="left:463px;background:linear-gradient(135deg,#f4eef0 0%,#e8a0b6 55%,#f3f0f0 100%)" role="img" aria-label="Model in pink costume on white sheets"></div>
<div class="cat-img" style="left:753px;background:linear-gradient(135deg,#c9ccd6 0%,#4b4f60 55%,#25262e 100%)" role="img" aria-label="Model in fishnet stockings and heels"></div>
<div class="cat-label" style="left:172px;top:1262px">Outdoor Videos</div>
<div class="cat-label" style="left:463px;top:1262px">Naughty Costumes</div>
<div class="cat-label" style="left:753px;top:1245px">Slutty<br>Whore-Shoes</div>

<!-- Videos -->
<h2 class="section-title" style="top:1418px">Our <span class="pink">Videos</span></h2>

<svg width="0" height="0" style="position:absolute">
  <defs>
    <g id="play-icon"><circle cx="20" cy="20" r="19" fill="#fff"/><path d="M15 11 L29 20 L15 29 Z" fill="#000"/></g>
    <g id="share-icon" fill="none" stroke="#ff0a78" stroke-width="1.6"><circle cx="14" cy="4" r="2.5"/><circle cx="4" cy="9" r="2.5"/><circle cx="14" cy="14" r="2.5"/><path d="M6.2 8 L11.8 5 M6.2 10 L11.8 13"/></g>
  </defs>
</svg>

<div class="card featured" style="left:172px;top:1542px">
  <div class="thumb" style="background:linear-gradient(135deg,#5a1010,#b8202a 60%,#3a2a20)" role="img" aria-label="Legs in red heels on a chair"><span class="tag">FREE</span><svg class="play" viewBox="0 0 40 40"><use href="#play-icon"/></svg></div>
  <div class="card-foot"><span class="avatar"></span><span class="caption">Lorem ipsum dolor sit ametetur ais</span><svg class="share" viewBox="0 0 18 18"><use href="#share-icon"/></svg></div>
</div>
<div class="card" style="left:391px;top:1542px">
  <div class="thumb" style="background:linear-gradient(135deg,#2a1c16,#6a5040 55%,#1a1410)" role="img" aria-label="Model on a leather sofa"><svg class="play" viewBox="0 0 40 40"><use href="#play-icon"/></svg></div>
  <div class="card-foot"><span class="avatar"></span><span class="caption">Lorem ipsum dolor sit ametetur ais</span><svg class="share" viewBox="0 0 18 18"><use href="#share-icon"/></svg></div>
</div>
<div class="card" style="left:611px;top:1542px">
  <div class="thumb" style="background:linear-gradient(135deg,#3a3a32,#b09070 55%,#2a2a24)" role="img" aria-label="Model in a dark bikini"><span class="tag">FREE</span><svg class="play" viewBox="0 0 40 40"><use href="#play-icon"/></svg></div>
  <div class="card-foot"><span class="avatar"></span><span class="caption">Lorem ipsum dolor sit ametetur ais</span><svg class="share" viewBox="0 0 18 18"><use href="#share-icon"/></svg></div>
</div>
<div class="card" style="left:829px;top:1542px">
  <div class="thumb" style="background:linear-gradient(135deg,#5a5248,#d8b8a0 55%,#3a3230)" role="img" aria-label="Model lying on a bed"><span class="tag">FREE</span><svg class="play" viewBox="0 0 40 40"><use href="#play-icon"/></svg></div>
  <div class="card-foot"><span class="avatar"></span><span class="caption">Lorem ipsum dolor sit ametetur ais</span><svg class="share" viewBox="0 0 18 18"><use href="#share-icon"/></svg></div>
</div>

<div class="card" style="left:172px;top:1813px">
  <div class="thumb" style="background:linear-gradient(135deg,#f0dccc,#c89a80 50%,#1a1616)" role="img" aria-label="Model in black lace"><svg class="play" viewBox="0 0 40 40"><use href="#play-icon"/></svg></div>
  <div class="card-foot"><span class="avatar"></span><span class="caption">Lorem ipsum dolor sit ametetur ais</span><svg class="share" viewBox="0 0 18 18"><use href="#share-icon"/></svg></div>
</div>
<div class="card" style="left:391px;top:1813px">
  <div class="thumb" style="background:linear-gradient(135deg,#0a0a0a,#6a4a3a 55%,#0a0a0a)" role="img" aria-label="Model in black on a dark background"><span class="tag">FREE</span><svg class="play" viewBox="0 0 40 40"><use href="#play-icon"/></svg></div>
  <div class="card-foot"><span class="avatar"></span><span class="caption">Lorem ipsum dolor sit ametetur ais</span><svg class="share" viewBox="0 0 18 18"><use href="#share-icon"/></svg></div>
</div>
<div class="card" style="left:611px;top:1813px">
  <div class="thumb" style="background:linear-gradient(135deg,#0a3a4a,#1a6a80 50%,#0a1a20)" role="img" aria-label="Pole dancer in the rain"><svg class="play" viewBox="0 0 40 40"><use href="#play-icon"/></svg></div>
  <div class="card-foot"><span class="avatar"></span><span class="caption">Lorem ipsum dolor sit ametetur ais</span><svg class="share" viewBox="0 0 18 18"><use href="#share-icon"/></svg></div>
</div>
<div class="card" style="left:829px;top:1813px">
  <div class="thumb" style="background:linear-gradient(135deg,#c07030,#e0a070 45%,#1a1210)" role="img" aria-label="Model in black lace stockings"><span class="tag">FREE</span><svg class="play" viewBox="0 0 40 40"><use href="#play-icon"/></svg></div>
  <div class="card-foot"><span class="avatar"></span><span class="caption">Lorem ipsum dolor sit ametetur ais</span><svg class="share" viewBox="0 0 18 18"><use href="#share-icon"/></svg></div>
</div>

<a class="btn btn-fill" style="left:512px;top:2097px;width:176px;height:49px">Upload Videos</a>

<!-- Membership -->
<section class="member"></section>
<div class="price-line"></div>
<div class="price">$25</div>
<h2 class="abs member-title">Monthly<br>Membership</h2>
<p class="abs member-text">Lorem ipsum dolor sit amet, consectetur adipiscing elit, sed do eiusmod tempor incididunt ut labLorem ipsum dolor sit amet, consectetur adipiscing elit, sed do eiusmod tempor incididunt ut lab</p>
<a class="btn btn-line" style="left:171px;top:2586px;width:124px;height:40px;font-size:22px">Join Now</a>
<div class="abs member-photo" role="img" aria-label="Smiling model in a pink bikini"></div>

<!-- Store -->
<h2 class="section-title" style="top:2787px">Our <span class="pink">Store</span></h2>

<div class="product" style="left:172px">
  <div class="product-img" style="top:8px;width:234px;height:150px;background:radial-gradient(ellipse at center,#c0187a 0%,#4a0a2e 55%,#111 100%)" role="img" aria-label="Pink toys"></div>
  <div class="product-name">Sex Toys</div>
  <div class="product-text" style="top:222px">Lorem ipsum dolor sit amet<br>consectetur adipisciab</div>
  <a class="btn btn-pink-line">Order Now</a>
</div>
<div class="product" style="left:473px">
  <div class="product-img" style="top:10px;width:120px;height:160px;background:linear-gradient(180deg,#ff2a94,#c0106a)" role="img" aria-label="Pink lace lingerie set"></div>
  <div class="product-name">Costumes</div>
  <div class="product-text" style="top:222px">Lorem ipsum dolor sit amet<br>consectetur adipisciab</div>
  <a class="btn btn-pink-line">Order Now</a>
</div>
<div class="product" style="left:775px">
  <div class="product-img" style="top:50px;width:130px;height:82px;border-radius:10px;background:linear-gradient(180deg,#ff3aa0,#b0105e)" role="img" aria-label="Pink compact camera"></div>
  <div class="product-name" style="top:180px">Outfits to wear<br>on camera</div>
  <div class="product-text" style="top:245px">Lorem ipsum dolor s</div>
  <a class="btn btn-pink-line">Order Now</a>
</div>

<!-- Latest stills -->
<section class="stills"></section>
<div class="abs stills-photo" role="img" aria-label="Two models in swimsuits and sunglasses"></div>
<svg class="arrow" style="left:112px" viewBox="0 0 36 68"><path d="M34 2 L2 34 L34 66" fill="none" stroke="#ff0a78" stroke-width="2"/></svg>
<svg class="arrow" style="left:1038px" viewBox="0 0 36 68"><path d="M2 2 L34 34 L2 66" fill="none" stroke="#ff0a78" stroke-width="2"/></svg>
<h2 class="abs stills-title">Latest <span class="pink">Stills</span></h2>
<p class="abs stills-text">Lorem ipsum dolor sit amet, consectetur adipiscing elit, sed do eiusmod tempor incididunt ut labLorem ipsum dolor sit amet, consectetur adipiscing elit, sed do eiusmod tempor incididunt ut lab</p>

<!-- Footer -->
<footer class="footer"></footer>
<div class="social" aria-label="Social links"><span></span><span></span><span></span><span></span><span></span></div>
<p class="copy">Copyright 2020 &nbsp;Sirena Blush.All Rights Reserved</p>
<div class="brand" style="left:484px;top:4024px;font-size:32px"><span class="brand-dot" style="width:30px;height:30px"></span>Sirena Blush</div>

</body>
</html>
```